Stationary for a Consulting Firm
The Summit Compass Incorporated
Project: Stationary for a Consulting Firm
Stationary for a Consulting Firm - Consulting
Creative Brief
Professional
Dr. Gordon T. Whitfield
President
214 Maple Ridge Lane Lakemont, ON K0Z 3K9
gwhitfield@summitcompass-example.ca
www.summitcompass-example.ca
Business Cards, Stationary, Fax Cover Sheet, and Envelopes are required
Canada's Summit Compass

```html
<!DOCTYPE html>
<html lang="en">
<head>
<meta charset="utf-8">
<title>Summit Compass – Business Card</title>
<link href="https://fonts.googleapis.com/css2?family=Open+Sans:wght@400;600&family=Montserrat:wght@800&display=swap" rel="stylesheet">
<style>
  :root {
    --bg: #e9ecef;
    --card-white: #ffffff;
    --blue: #2f9bd6;
    --blue-deep: #1f86c4;
    --blue-light: #9fd2ee;
    --blue-pale: #d6edf9;
    --text-light: #ffffff;
    --shadow: rgba(20, 40, 60, 0.18);
  }
  * { box-sizing: border-box; margin: 0; padding: 0; }
  html, body {
    width: 1200px; height: 980px; overflow: hidden;
    background: var(--bg);
    font-family: "Open Sans", Arial, sans-serif;
  }
  .card {
    position: absolute; left: 250px;
    width: 700px; height: 400px;
    border-radius: 26px; overflow: hidden;
    box-shadow: 0 10px 30px var(--shadow);
  }
  .card--front { top: 60px; background: var(--card-white); }
  .card--back {
    top: 520px;
    background: linear-gradient(160deg, #45abe0 0%, var(--blue) 55%, var(--blue-deep) 100%);
  }
  .card__waves { position: absolute; inset: 0; width: 100%; height: 100%; }

  .brand {
    position: absolute; left: 330px; top: 48px; width: 200px;
    text-align: center;
  }
  .brand__mark {
    width: 76px; height: 76px; margin: 0 auto 10px;
    border-radius: 50%; background: var(--blue);
  }
  .brand__name {
    font-family: "Montserrat", Arial, sans-serif; font-weight: 800;
    color: var(--blue-deep); font-size: 26px; line-height: 1.05;
    letter-spacing: 1px;
  }

  .contact {
    position: absolute; left: 28px; top: 200px;
    list-style: none; color: var(--text-light); font-size: 12px;
  }
  .contact__item {
    display: flex; align-items: center; gap: 8px;
    height: 22px;
  }
  .contact__item--address { height: 34px; line-height: 1.3; }
  .contact__icon { width: 14px; height: 14px; flex: none; }

  .person {
    position: absolute; right: 34px; bottom: 30px;
    text-align: right; color: var(--text-light);
  }
  .person__name { font-weight: 600; font-size: 13px; }
  .person__title { font-size: 11px; }

  .back__web {
    position: absolute; left: 30px; top: 26px;
    color: var(--text-light); font-size: 13px; letter-spacing: 1.5px;
  }
  .back__circle {
    position: absolute; right: 50px; bottom: 40px;
    width: 130px; height: 130px; border-radius: 50%;
    background: rgba(255, 255, 255, 0.14);
  }
</style>
</head>
<body>

<section class="card card--front">
  <svg class="card__waves" viewBox="0 0 700 400" preserveAspectRatio="none" aria-hidden="true">
    <path d="M0,128 C200,148 400,292 700,292 L700,312 C400,312 200,168 0,148 Z" fill="var(--blue-pale)"/>
    <path d="M0,140 C200,160 400,300 700,300 L700,312 C400,312 200,172 0,152 Z" fill="var(--blue-light)"/>
    <path d="M0,150 C200,170 400,310 700,310 L700,400 L0,400 Z" fill="var(--blue)"/>
  </svg>

  <div class="brand">
    <div class="brand__mark"></div>
    <div class="brand__name">SUMMIT<br>COMPASS</div>
  </div>

  <ul class="contact">
    <li class="contact__item contact__item--address">
      <svg class="contact__icon" viewBox="0 0 14 14"><circle cx="7" cy="7" r="7" fill="#fff"/><path d="M7 3a2.4 2.4 0 0 0-2.4 2.4C4.6 7.3 7 10.5 7 10.5s2.4-3.2 2.4-5.1A2.4 2.4 0 0 0 7 3z" fill="var(--blue)"/></svg>
      <span>214 Maple Ridge Lane<br>Lakemont, ON K0Z 3K9</span>
    </li>
    <li class="contact__item">
      <svg class="contact__icon" viewBox="0 0 14 14"><circle cx="7" cy="7" r="7" fill="#fff"/><path d="M4.5 3.5h1.6l.7 1.8-1 .7a5 5 0 0 0 2.2 2.2l.7-1 1.8.7v1.6c0 .5-.4.8-.9.8A6 6 0 0 1 3.7 4.4c0-.5.3-.9.8-.9z" fill="var(--blue)"/></svg>
      <span>(555) 201-0148</span>
    </li>
    <li class="contact__item">
      <svg class="contact__icon" viewBox="0 0 14 14"><circle cx="7" cy="7" r="7" fill="#fff"/><path d="M4.5 3.5h1.6l.7 1.8-1 .7a5 5 0 0 0 2.2 2.2l.7-1 1.8.7v1.6c0 .5-.4.8-.9.8A6 6 0 0 1 3.7 4.4c0-.5.3-.9.8-.9z" fill="var(--blue)"/></svg>
      <span>(555) 318-0173</span>
    </li>
    <li class="contact__item">
      <svg class="contact__icon" viewBox="0 0 14 14"><circle cx="7" cy="7" r="7" fill="#fff"/><rect x="3.5" y="4.5" width="7" height="5" fill="var(--blue)"/><path d="M3.5 4.5 7 7.3l3.5-2.8" stroke="#fff" stroke-width="0.8" fill="none"/></svg>
      <span>gwhitfield@summitcompass-example.ca</span>
    </li>
    <li class="contact__item">
      <svg class="contact__icon" viewBox="0 0 14 14"><circle cx="7" cy="7" r="7" fill="#fff"/><circle cx="7" cy="7" r="3.6" stroke="var(--blue)" stroke-width="1" fill="none"/><path d="M3.4 7h7.2M7 3.4c-1.6 2-1.6 5.2 0 7.2M7 3.4c1.6 2 1.6 5.2 0 7.2" stroke="var(--blue)" stroke-width="0.8" fill="none"/></svg>
      <span>www.summitcompass-example.ca</span>
    </li>
  </ul>

  <div class="person">
    <p class="person__name">Dr. Gordon T. Whitfield</p>
    <p class="person__title">President</p>
  </div>
</section>

<section class="card card--back">
  <p class="back__web">www.summitcompass-example.ca</p>
  <div class="back__circle"></div>
</section>

</body>
</html>
```